Bramblewood Card Company Business Cards

We are a trading card store with Glimmorax, sports and other TCG cards, we need a business card design that encompasses a clean cut, modern style with a retro flare. website is bramblewoodcardco.com for reference. Can utilize a comic book era feel or a more modern outdoor feel to utilize the "Pacific Northwest" elements of tress, mountains, etc.

Industry/Entity Type

Trading cards and collectibles

Contact Information for Business Card

business name, email address, phone number, name, owner job title

Font styles to use
Sans Serif

```html
<!DOCTYPE html>
<html lang="en">
<head>
<meta charset="utf-8">
<title>Bramblewood Card Company – Business Cards</title>
<link rel="stylesheet" href="https://fonts.googleapis.com/css2?family=Montserrat:wght@400;500;700;800&display=swap">
<style>
  :root {
    --backdrop: #3b3b3b;
    --card: #ffffff;
    --slate: #6b6b6b;
    --ink: #1f1f1f;
    --cyan: #10bfe0;
  }
  * { box-sizing: border-box; margin: 0; padding: 0; }
  html, body {
    width: 1200px; height: 689px; overflow: hidden;
    background: var(--backdrop);
    font-family: "Montserrat", sans-serif;
  }
  .stage { position: relative; width: 1200px; height: 689px; }
  .card {
    position: absolute; top: 190px;
    width: 540px; height: 309px;
    background: var(--card);
    border-radius: 22px;
  }
  .card--front { left: 40px; }
  .card--back { left: 620px; }

  .brand-mark {
    position: absolute;
    display: flex; align-items: center; gap: 12px;
  }
  .brand-mark__square {
    width: 18px; height: 18px; background: var(--cyan); flex: none;
  }
  .brand-mark__name {
    color: var(--slate);
    font-weight: 800;
    text-transform: uppercase;
    line-height: 1.05;
    letter-spacing: 0.02em;
  }
  .card--front .brand-mark { left: 0; right: 0; top: 0; bottom: 0; justify-content: center; }
  .card--front .brand-mark__name { font-size: 30px; }
  .card--back .brand-mark { left: 32px; top: 0; bottom: 0; width: 190px; }
  .card--back .brand-mark__square { width: 14px; height: 14px; }
  .card--back .brand-mark__name { font-size: 19px; }

  .divider {
    position: absolute; left: 246px; top: 70px;
    width: 2px; height: 170px; background: var(--cyan);
  }
  .contact { position: absolute; left: 268px; top: 66px; }
  .contact__name {
    color: var(--cyan); font-weight: 800; font-size: 28px; letter-spacing: 0.01em; line-height: 1;
  }
  .contact__title { color: var(--ink); font-size: 14px; margin-top: 6px; }
  .contact__region { color: var(--cyan); font-size: 14px; margin-top: 14px; }
  .contact__address { color: var(--ink); font-size: 14px; margin-top: 2px; }
  .contact__list { list-style: none; margin-top: 14px; }
  .contact__item {
    display: flex; align-items: center; gap: 8px;
    color: var(--ink); font-size: 14px; line-height: 22px;
  }
  .contact__icon { width: 13px; height: 13px; fill: var(--cyan); flex: none; }
</style>
</head>
<body>
<main class="stage">
  <section class="card card--front" aria-label="Business card front">
    <div class="brand-mark">
      <span class="brand-mark__square"></span>
      <span class="brand-mark__name">Bramblewood<br>Card Company</span>
    </div>
  </section>

  <section class="card card--back" aria-label="Business card back">
    <div class="brand-mark">
      <span class="brand-mark__square"></span>
      <span class="brand-mark__name">Bramblewood<br>Card Company</span>
    </div>
    <div class="divider"></div>
    <div class="contact">
      <h1 class="contact__name">JORDAN HALE</h1>
      <p class="contact__title">Managing Director</p>
      <p class="contact__region">Pacific Northwest</p>
      <p class="contact__address">Your address, City</p>
      <ul class="contact__list">
        <li class="contact__item">
          <svg class="contact__icon" viewBox="0 0 16 16" aria-hidden="true"><path d="M3 1h3l1.5 4-2 1.3a9 9 0 0 0 4.2 4.2L11 8.5l4 1.5v3a2 2 0 0 1-2 2A12 12 0 0 1 1 3a2 2 0 0 1 2-2z"/></svg>
          123 456 789
        </li>
        <li class="contact__item">
          <svg class="contact__icon" viewBox="0 0 16 16" aria-hidden="true"><path d="M1 3h14v10H1zM2.5 4.5 8 9l5.5-4.5v-.5h-11z"/></svg>
          info@bramblewoodcardco.com
        </li>
        <li class="contact__item">
          <svg class="contact__icon" viewBox="0 0 16 16" aria-hidden="true"><circle cx="8" cy="8" r="7"/></svg>
          www.bramblewoodcardco.com
        </li>
      </ul>
    </div>
  </section>
</main>
</body>
</html>
```